Foot and ankle surgeon requires a website design

I need a website where prospective and established patients can obtain information and then direct them to making appointments. My practice is a highly professional surgical practice specialising in surgery to the foot and ankle. My title is Mr Colin Brasket, Podiatric Foot & Ankle Surgeon. My qualifications are: BSc MSc FACPS
The practice website will require information on: Locations, phone numbers to make appointments, general background on podiatric surgery,
I would like to include information on: my hospital appointments, surgical fellowships held, training programs undertaken, association memberships, publications written, links to useful websites
A page dedicated to common foot conditions would be useful and also a page with referral information including an online registration section that will be sent direct to the receptionist.
Examples of similar websites include:
http://www.dorvelquintaro.com.au/
http://www.haldenfootsurgeon.com.au/
I will provide files on logo, self photos and my personal training history etc.
Also if there is going to be a background theme I personally am associated with surfing and beach activities, it would be great if this was able to be reflected in the design.
Thank you.

```html
<!DOCTYPE html>
<html lang="en">
<head>
<meta charset="utf-8">
<title>Mr Colin Brasket – Podiatric Foot &amp; Ankle Surgeon</title>
<link rel="stylesheet" href="https://fonts.googleapis.com/css2?family=Crimson+Text:wght@400;700&family=Open+Sans:wght@400;600&family=Varela+Round&display=swap">
<style>
:root{
  --orange:#ee7a14;
  --orange-light:#f7a04a;
  --orange-dark:#e2660a;
  --navy:#0d4a86;
  --blue:#0b5f97;
  --text:#6b6b6b;
  --heading:#333;
  --border:#dcdcdc;
  --footer-top:#0b6aa2;
  --footer-bottom:#0a3b74;
}
*{margin:0;padding:0;box-sizing:border-box}
html,body{width:1103px;height:1200px;overflow:hidden;background:#fff}
body{position:relative;font-family:"Open Sans",sans-serif;color:var(--text)}
.abs{position:absolute}

/* header */
.brand{left:142px;top:52px;display:flex;align-items:center;gap:10px}
.brand-mark{width:34px;height:34px;border-radius:50%;background:var(--orange)}
.brand-name{font-family:"Crimson Text",serif;font-weight:700;font-size:25px;color:var(--navy);line-height:1}
.brand-tag{font-family:"Crimson Text",serif;font-weight:700;font-size:12.5px;color:var(--orange);margin-top:3px}
.appointment{right:138px;top:74px;text-align:right;font-family:"Varela Round",sans-serif}
.appointment-label{font-size:15px;color:var(--orange-light)}
.appointment-phone{font-size:18px;color:var(--blue);margin-top:3px}

/* nav */
.main-nav{left:129px;top:130px;width:845px;height:62px;border-radius:9px 9px 0 0;
  background:linear-gradient(var(--orange-light),var(--orange) 55%,var(--orange-dark));
  display:flex;font-family:"Varela Round",sans-serif;color:#fff}
.nav-item{display:flex;flex-direction:column;justify-content:center;align-items:center;
  border-right:1px solid rgba(255,255,255,.35);font-size:16px;line-height:1.2;text-align:center}
.nav-item:last-child{border-right:0}
.nav-item small{font-size:12px;display:block}

/* hero */
.hero{left:129px;top:192px;width:845px;height:336px;border-radius:0 0 9px 9px;overflow:hidden;
  background:linear-gradient(100deg,#6f9a4a 0%,#9fbf6a 30%,#c8c9c2 48%,#8a6a54 65%,#3a3a44 85%,#c0b6a4 100%)}
.hero-dots{left:520px;top:504px;display:flex;gap:5px}
.hero-dots span{width:12px;height:12px;border-radius:50%;background:#111}

/* feature strip */
.feature-title{left:132px;top:562px;font-family:"Varela Round",sans-serif;font-size:23px;color:var(--heading);letter-spacing:.2px}
.feature-sub{left:134px;top:592px;font-family:"Varela Round",sans-serif;font-size:14px;color:#888}
.btn-learn{left:848px;top:568px;width:116px;height:32px;border-radius:3px;
  background:linear-gradient(#1469a6,#0b3f74);color:#fff;font-family:"Varela Round",sans-serif;
  font-size:12.5px;display:flex;align-items:center;justify-content:center}
.divider{left:142px;top:637px;width:833px;height:1px;background:var(--border)}

/* welcome */
.welcome{left:131px;top:688px;width:425px}
.welcome h1{font-family:"Crimson Text",serif;font-weight:400;font-size:29px;color:var(--orange);line-height:1.1;margin-bottom:8px}
.welcome p{font-size:11px;line-height:16.6px;margin-bottom:6px}

.card{top:685px;width:196px;height:189px;border:1px solid var(--border);border-radius:8px}
.card-surgery{left:574px}
.card-photo{position:absolute;left:12px;top:11px;width:171px;height:92px;border-radius:7px;
  background:linear-gradient(120deg,#7a9a96,#d9c7bb 55%,#c7b3aa)}
.card-title{position:absolute;left:15px;top:113px;font-family:"Varela Round",sans-serif;font-size:17.5px;color:var(--orange)}
.card-text{position:absolute;left:15px;top:140px;width:170px;font-size:10px;line-height:16.5px;color:#888}
.card-training{left:779px}
.card-training h2{position:absolute;left:17px;top:17px;font-family:"Varela Round",sans-serif;font-weight:400;font-size:18px;color:var(--blue)}
.training-list{position:absolute;left:22px;top:47px;list-style:none;font-size:11px;color:var(--navy)}
.training-list li{height:20.7px;display:flex;align-items:center;gap:7px}
.training-list li::before{content:"";border-left:4px solid var(--navy);border-top:4px solid transparent;border-bottom:4px solid transparent}

/* footer */
.site-footer{left:0;top:951px;width:1103px;height:249px;background:linear-gradient(var(--footer-top),var(--footer-bottom));color:#fff}
.footer-heading{font-family:"Varela Round",sans-serif;font-size:15.5px;top:37px}
.footer-col{font-size:11px;line-height:22px}
.loc{font-size:11px;line-height:19.7px}
.loc strong{font-weight:600}
.footer-rule{left:129px;top:193px;width:845px;height:1px;background:rgba(255,255,255,.15)}
.copyright{left:132px;top:211px;font-size:10px;color:rgba(255,255,255,.35)}
.social{left:868px;top:207px;display:flex;gap:3px}
.social span{width:24px;height:24px;border-radius:50%;background:#fff}
</style>
</head>
<body>

<header>
  <div class="abs brand">
    <span class="brand-mark"></span>
    <div>
      <div class="brand-name">Mr Colin Brasket</div>
      <div class="brand-tag">Podiatric Foot &amp; Ankle Surgeon</div>
    </div>
  </div>
  <div class="abs appointment">
    <div class="appointment-label">Make Appointment</div>
    <div class="appointment-phone">08 9970 2146 / 08 9970 2158</div>
  </div>
</header>

<nav class="abs main-nav">
  <div class="nav-item" style="width:86px">Home</div>
  <div class="nav-item" style="width:125px">Appointments</div>
  <div class="nav-item" style="width:94px">Surgical<small>Fellowships</small></div>
  <div class="nav-item" style="width:90px">Training<small>Programs</small></div>
  <div class="nav-item" style="width:124px">Memberships</div>
  <div class="nav-item" style="width:114px">Publications</div>
  <div class="nav-item" style="width:85px">Useful<small>Websites</small></div>
  <div class="nav-item" style="width:127px">Contact Us</div>
</nav>

<div class="abs hero" role="img" aria-label="Photo of a runner holding his ankle above a white sports shoe, outdoors by greenery and water"></div>
<div class="abs hero-dots"><span></span><span></span><span></span><span></span></div>

<div class="abs feature-title">DUIS TINCIDUNT LECTUS DUI VIVERRA VESTIBULUM</div>
<div class="abs feature-sub">Mauris vel lacus vitae felis vestibulum volutpat Etiam est nunc venenatis in tristique eu imperdiet ac nisl</div>
<div class="abs btn-learn">LEARN MORE</div>
<div class="abs divider"></div>

<section class="abs welcome">
  <h1>Welcome to Our Website Mainpage</h1>
  <p>For those unfamiliar with our services, we are a team of accredited health professionals dealing with the prevention, diagnosis, treatment and rehabilitation of medical and surgical conditions related to feet, ankles and lower limbs.</p>
  <p>The Coastal Foot Health Group have practices based throughout regional Western Australia in Geraldton and Kalgoorlie and offer the following services; sports injuries, foot care, foot orthoses and diabetes care. Many foot and lower limb problems, if identified early can be prevented, so take the right step and contact the Coastal Foot Health Group for advice on your foot, ankle, heel or leg pain or sports injury.</p>
</section>

<article class="abs card card-surgery">
  <div class="card-photo" role="img" aria-label="Close-up photo of a gloved hand treating a patient's foot"></div>
  <div class="card-title">Ankle Surgery</div>
  <p class="card-text">Morbi magna magna tincidunt a mattis non imperdiet vitae</p>
</article>

<article class="abs card card-training">
  <h2>Training Program</h2>
  <ul class="training-list">
    <li>Bunions</li>
    <li>Tailors Bunion Deformity</li>
    <li>Big Toe Joint Arthritis</li>
    <li>Hammertoe Deformity</li>
    <li>Ingrown Toenails</li>
    <li>Neuroma</li>
  </ul>
</article>

<footer class="abs site-footer">
  <div class="abs footer-heading" style="left:130px">QUICK LINKS</div>
  <div class="abs footer-col" style="left:131px;top:58px">Home<br>Appointments<br>Surgical fellowships</div>
  <div class="abs footer-col" style="left:258px;top:58px">Training programs<br>Memberships<br>Publications</div>
  <div class="abs footer-col" style="left:384px;top:58px">Useful websites<br>Contact us</div>

  <div class="abs footer-heading" style="left:510px">LOCATIONS</div>
  <div class="abs loc" style="left:512px;top:60px"><strong>Geraldton</strong><br>48 Seabreeze Parade,<br>PO BOX 2207,<br>Geraldton WA 6530<br>Ph: 08 9970 2158</div>
  <div class="abs loc" style="left:712px;top:58px"><strong>West End, Geraldton</strong><br>7A &amp; 7B Tidewater Lane,<br>Geraldton 6530.<br>Ph: 9970 3312<br>Fax: 9970 3319</div>
  <div class="abs loc" style="left:870px;top:58px"><strong>Kalgoorlie</strong><br>3/14 Saltbush Rd,<br>Kalgoorlie WA 6430<br>Ph: 08 9088 1520<br>Fax: 08 9088 1534</div>

  <div class="abs footer-rule"></div>
  <div class="abs copyright">© 2014 Company Name &nbsp;All right reserved &nbsp;Term of Use</div>
  <div class="abs social"><span></span><span></span><span></span><span></span></div>
</footer>

</body>
</html>
```